Accounting firm needing business card / letterhead designed
Marcus L. Trenholm, CPA
marcus@veltrowledger.com
www.veltrowledger.com
842 E Alder Ave Calvenport, ND 43827
419-562-0974

```html
<!DOCTYPE html>
<html lang="en">
<head>
<meta charset="utf-8">
<title>Veltrow Ledger — Business Card</title>
<link rel="stylesheet" href="https://fonts.googleapis.com/css2?family=Barlow:wght@500&family=Barlow+Semi+Condensed:wght@600;700&display=swap">
<style>
  :root {
    --backdrop: #e6e6e6;
    --card: #f7f7f7;
    --card-shade: #ececec;
    --navy: #24164b;
    --green: #5db52c;
    --ink: #1c1c24;
  }
  * { margin: 0; padding: 0; box-sizing: border-box; }
  html, body {
    width: 1200px;
    height: 576px;
    overflow: hidden;
    background: var(--backdrop);
  }
  .canvas {
    position: relative;
    width: 1200px;
    height: 576px;
  }
  .card {
    position: absolute;
    border-radius: 13px;
    background: linear-gradient(180deg, var(--card) 0%, var(--card-shade) 100%);
    box-shadow: 0 3px 6px rgba(0,0,0,0.25);
    overflow: hidden;
  }
  .card--front { left: 82px; top: 139px; width: 485px; height: 293px; }
  .card--back  { left: 603px; top: 138px; width: 480px; height: 291px; }

  .holder-name {
    position: absolute;
    left: 30px;
    top: 38px;
    font-family: "Barlow Semi Condensed", sans-serif;
    font-weight: 700;
    font-size: 19px;
    color: var(--navy);
    letter-spacing: 0.1px;
  }
  .holder-name .credential { color: var(--green); }

  .contact-list {
    position: absolute;
    left: 36px;
    top: 68px;
    list-style: none;
    font-family: "Barlow", sans-serif;
    font-weight: 500;
    font-size: 11.5px;
    color: var(--ink);
  }
  .contact-list li {
    display: flex;
    align-items: center;
    height: 15.2px;
  }
  .contact-icon {
    width: 10px;
    height: 10px;
    margin-right: 8px;
    flex: none;
  }
  .address {
    position: absolute;
    left: 30px;
    top: 119px;
    font-family: "Barlow", sans-serif;
    font-weight: 500;
    font-size: 11.5px;
    color: var(--ink);
  }

  .brand-name {
    position: absolute;
    font-family: "Barlow Semi Condensed", sans-serif;
    font-weight: 700;
    font-size: 34px;
    line-height: 1;
    color: var(--navy);
    letter-spacing: 0.5px;
    white-space: nowrap;
  }
  .card--front .brand-name { left: 32px; top: 222px; }
  .card--back .brand-name { right: 35px; top: 220px; }
</style>
</head>
<body>
<main class="canvas">
  <section class="card card--front" aria-label="Card front">
    <h1 class="holder-name">Marcus L. Trenholm, <span class="credential">CPA</span></h1>
    <ul class="contact-list">
      <li>
        <svg class="contact-icon" viewBox="0 0 10 10" aria-hidden="true">
          <path d="M1 3 Q5 0.5 9 3 L8 4.3 L6.5 3.6 L6.5 3 Q5 2.5 3.5 3 L3.5 3.6 L2 4.3 Z" fill="var(--green)"/>
          <path d="M2.5 5 L7.5 5 L8.5 9 L1.5 9 Z" fill="var(--green)"/>
        </svg>
        419-562-0974
      </li>
      <li>
        <svg class="contact-icon" viewBox="0 0 10 10" aria-hidden="true">
          <rect x="0.5" y="2" width="9" height="6.5" fill="var(--green)"/>
          <path d="M0.8 2.3 L5 5.8 L9.2 2.3" fill="none" stroke="#fff" stroke-width="0.9"/>
        </svg>
        marcus@veltrowledger.com
      </li>
      <li>
        <svg class="contact-icon" viewBox="0 0 10 10" aria-hidden="true">
          <circle cx="5" cy="5" r="4.4" fill="var(--green)"/>
          <g fill="none" stroke="#fff" stroke-width="0.7">
            <ellipse cx="5" cy="5" rx="1.8" ry="4.4"/>
            <line x1="0.6" y1="5" x2="9.4" y2="5"/>
          </g>
        </svg>
        www.veltrowledger.com
      </li>
    </ul>
    <p class="address">842 E Alder Ave Calvenport, ND 43827</p>
    <p class="brand-name">Veltrow Ledger</p>
  </section>

  <section class="card card--back" aria-label="Card back">
    <p class="brand-name">Veltrow Ledger</p>
  </section>
</main>
</body>
</html>
```